Gobal construction supply company needs new business card design

I need a business card design for my global supply company using an existing logo. i will be looking to print these on rounded corner cards with the black background version of my logo on the back. on the front white background, my logo again and my simple details.

```html
<!DOCTYPE html>
<html lang="en">
<head>
<meta charset="utf-8">
<title>Meridian Build Supply – Business Card</title>
<link rel="stylesheet" href="https://fonts.googleapis.com/css2?family=Montserrat:wght@600;700&family=Open+Sans:wght@400&display=swap">
<style>
  :root {
    --backdrop: #5f5f5f;
    --card-light: #f2f2f2;
    --card-dark: #141414;
    --ink: #111111;
    --accent: #e0000f;
    --divider: #c9c9c9;
    --white: #ffffff;
  }
  * { margin: 0; padding: 0; box-sizing: border-box; }
  html, body { width: 1200px; height: 802px; overflow: hidden; }
  body { background: var(--backdrop); position: relative; font-family: "Open Sans", sans-serif; }

  .card {
    position: absolute;
    top: 274px;
    width: 443px;
    height: 265px;
    border-radius: 16px;
    box-shadow: 3px 4px 6px rgba(0,0,0,0.45);
  }
  .card--front { left: 136px; background: var(--card-light); }
  .card--back { left: 624px; background: var(--card-dark); }

  .brand {
    position: absolute;
    display: flex;
    align-items: center;
    gap: 8px;
    font-family: "Montserrat", sans-serif;
    font-weight: 700;
    letter-spacing: 0.5px;
  }
  .brand__mark { width: 16px; height: 16px; background: var(--accent); }
  .brand__dot { width: 20px; height: 20px; border-radius: 50%; background: var(--accent); }

  .card--front .brand { left: 30px; top: 108px; font-size: 27px; color: var(--ink); }

  .divider {
    position: absolute;
    left: 221px; top: 80px;
    width: 1px; height: 106px;
    background: var(--divider);
  }

  .details { position: absolute; left: 247px; top: 84px; color: var(--ink); }
  .details__name {
    font-family: "Montserrat", sans-serif;
    font-weight: 700;
    font-size: 16px;
    color: var(--accent);
    line-height: 18px;
  }
  .details__role { font-size: 12.5px; line-height: 15px; margin-bottom: 9px; }
  .contact { list-style: none; }
  .contact li {
    display: flex; align-items: center; gap: 6px;
    font-size: 12.5px; line-height: 15.8px;
  }
  .contact svg { width: 9px; height: 9px; flex: none; fill: var(--accent); }

  .card--back .brand {
    left: 0; right: 0; top: 112px;
    justify-content: center;
    font-size: 34px;
    color: var(--white);
    gap: 12px;
  }
</style>
</head>
<body>
  <section class="card card--front">
    <div class="brand"><span class="brand__name">MERIDIAN</span><span class="brand__mark"></span></div>
    <div class="divider"></div>
    <div class="details">
      <p class="details__name">DANIEL HARPER</p>
      <p class="details__role">Managing Director</p>
      <ul class="contact">
        <li><svg viewBox="0 0 10 10"><path d="M1 3.5C1 2 2.5 1.5 5 1.5S9 2 9 3.5L7.5 4 7 3H3L2.5 4zM2.5 4.5h5L8.5 8.5h-7z"/></svg>044-210 387 615</li>
        <li><svg viewBox="0 0 10 10"><path d="M2.5 0.5h5v9h-5zM3.5 1.5v6h3v-6z"/></svg>044-210 387 615</li>
        <li><svg viewBox="0 0 10 10"><path d="M0.5 2h9v6h-9zM1.5 2.8 5 5.6 8.5 2.8v-0.2h-7z"/></svg>info@meridianbuild.com</li>
        <li><svg viewBox="0 0 10 10"><circle cx="5" cy="5" r="4.5"/></svg>www.meridianbuild.com</li>
      </ul>
    </div>
  </section>

  <section class="card card--back">
    <div class="brand"><span class="brand__name">MERIDIAN</span><span class="brand__dot"></span></div>
  </section>
</body>
</html>
```